Spring Savings Package for The Lodge at Harrow Meadow Lodge

Design an email and elevator poster 11x7 that promotes Spring and our heated pools at The Lodge at Harrow Meadow
Text-

Worried about the Spring Weather don't #CoveSplashHall !

Ask about our Blossom Break Deal that comes with a Free Resort Beach Towel ($12 value).

Book by March 1st,2019
Stay Dates Now-May 23rd,2019

Phone number: 800.555.0148

Reserve Now! www (dot) lodgeatharrowmeadow-example (dot) com

Target Market(s)

Guest reserving Spring Break

Industry/Entity Type

Hospitality

Requirements
Must have
• text
• phone
• website
• Book Now
• Can change some of the text to make it more of a Sales piece
Nice to have
• Brand Colors

```html
<!DOCTYPE html>
<html lang="en">
<head>
<meta charset="utf-8">
<title>Blossom Break Deal – The Lodge at Harrow Meadow</title>
<link rel="stylesheet" href="https://fonts.googleapis.com/css2?family=Tinos:wght@400;700&family=Roboto+Condensed:wght@700&family=Cinzel+Decorative:wght@400&display=swap">
<style>
  :root{
    --page:#7a7a78;
    --white:#ffffff;
    --header-bg:#f6f6f6;
    --tan:#d6a05e;
    --navy:#262a6e;
    --headline-blue:#1e6a9e;
    --body-grey:#555555;
    --orange:#f0a04b;
    --sky-card:#e6f3fc;
    --lemon-card:#fdfab7;
    --save-blue:#1f7cc4;
    --save-gold:#d49a12;
    --panel-grey:#efefef;
    --wave:#5a7d8c;
    --hero-blue:#5cbde9;
    --hero-mist:#b4dcef;
    --hero-green:#a9cf86;
  }
  *{box-sizing:border-box;margin:0;padding:0}
  html,body{width:1200px;height:2293px;overflow:hidden;background:var(--page)}
  body{font-family:"Tinos",serif;position:relative}
  .email{position:absolute;left:32px;top:29px;width:1139px;height:2235px;background:var(--white);overflow:hidden}

  .masthead{position:absolute;left:0;top:0;width:100%;height:222px;background:var(--header-bg)}
  .brand{position:absolute;left:34px;top:78px;display:flex;align-items:center;gap:14px;
    font-family:"Tinos",serif;font-weight:700;font-size:31px;line-height:1.1;color:var(--tan);width:320px}
  .brand-mark{width:22px;height:22px;background:var(--tan);flex:none}
  .phone{position:absolute;right:42px;top:114px;font-size:33px;color:var(--navy)}

  .nav{position:absolute;left:0;top:222px;width:100%;height:60px;background:var(--tan)}
  .nav a{color:var(--white);text-decoration:none;font-size:27px;position:absolute;top:14px}

  .hero{position:absolute;left:0;top:282px;width:100%;height:581px;
    background:linear-gradient(160deg,var(--hero-blue) 0%,var(--hero-mist) 50%,var(--hero-green) 100%)}
  .hero svg{position:absolute;left:0;top:0}

  .intro{position:absolute;left:0;top:900px;width:100%;text-align:center}
  .headline{font-weight:700;font-size:33px;line-height:40px;color:var(--headline-blue);letter-spacing:1px;text-transform:uppercase}
  .lede{margin-top:14px;font-size:26px;line-height:38px;color:var(--body-grey)}

  .deal-title{position:absolute;left:0;top:1168px;width:100%;display:flex;justify-content:center;align-items:center;gap:28px}
  .deal-title h2{font-family:"Cinzel Decorative",serif;font-weight:400;font-size:44px;line-height:52px;color:var(--orange);letter-spacing:1px}
  .bloom{width:44px;height:44px;border-radius:50%;background:#e8803a}

  .offers{position:absolute;left:0;top:1239px;width:100%;height:556px;display:flex;gap:4px}
  .offer{flex:1;display:flex;flex-direction:column}
  .offer.sky{background:var(--sky-card)}
  .offer.lemon{background:var(--lemon-card)}
  .offer-name{height:148px;display:flex;align-items:center;justify-content:center;text-align:center;
    font-family:"Tinos",serif;font-weight:700;font-size:42px;line-height:1.05}
  .sky .offer-name{color:var(--save-blue)}
  .lemon .offer-name{color:#222222;font-size:34px}
  .offer-name.summer{font-size:50px;line-height:0.95}
  .offer-photo{height:267px}
  .offer-save{height:141px;display:flex;align-items:center;justify-content:center;gap:10px;
    font-family:"Roboto Condensed",sans-serif;font-weight:700}
  .save-label{font-size:38px;line-height:36px;text-align:center}
  .save-num{font-size:76px;line-height:1}
  .save-num sup{font-size:36px;vertical-align:30px}
  .sky .offer-save{color:var(--save-blue)}
  .lemon .offer-save{color:var(--save-gold)}

  .booking{position:absolute;left:0;top:1795px;width:100%;height:281px;background:var(--panel-grey);text-align:center;color:var(--navy)}
  .booking p{font-size:33px;line-height:56px}
  .booking .dates{padding-top:34px}
  .reserve{display:inline-block;margin-top:28px;width:320px;height:76px;line-height:76px;background:var(--navy);
    color:var(--white);font-weight:700;font-size:29px;text-decoration:none}

  .footer{position:absolute;left:0;top:2076px;width:100%;height:159px;background:var(--tan);text-align:center;color:var(--white)}
  .footer .site{padding-top:36px;font-size:31px}
  .footer .copy{margin-top:14px;font-size:21px}
</style>
</head>
<body>
<div class="email">

  <header class="masthead">
    <div class="brand"><span class="brand-mark"></span><span>The Lodge at Harrow Meadow</span></div>
    <div class="phone">Phone : 800.555.0148</div>
  </header>

  <nav class="nav">
    <a style="left:55px">GUEST ROOMS</a>
    <a style="left:335px">WATERPARK</a>
    <a style="left:587px">DISCOUNTS</a>
    <a style="left:872px">RECREATION</a>
  </nav>

  <section class="hero" role="img" aria-label="Photo banner: girls relaxing on pool floats in front of the lodge, framed by a sunny spring meadow scene">
    <svg width="1139" height="581" viewBox="0 0 1139 581" aria-hidden="true">
      <path d="M0 520 C300 590 800 600 1139 430 L1139 581 L0 581 Z" fill="#ffffff"/>
      <path d="M0 520 C300 590 800 600 1139 430" fill="none" stroke="var(--wave)" stroke-width="9"/>
    </svg>
  </section>

  <section class="intro">
    <h1 class="headline">Worried about the weather<br>don't #HeatedPools !</h1>
    <p class="lede">Ask about our Blossom Break Deal that comes with a<br>Free Willow Falls Waterpark Resort Beach Towel ($12 value). PLUS!<br>A Mountain Breakfast at Nana's Hearth Kitchen is included with all stays.</p>
  </section>

  <div class="deal-title">
    <span class="bloom" role="img" aria-label="Flower ornament"></span>
    <h2>Blossom Break Deal</h2>
    <span class="bloom" role="img" aria-label="Flower ornament"></span>
  </div>

  <section class="offers">
    <article class="offer sky">
      <div class="offer-name">Splash Meadow</div>
      <div class="offer-photo" role="img" aria-label="Girl splashing out of a yellow slide into the pool" style="background:linear-gradient(180deg,#b9b3a6,#6fa9b8)"></div>
      <div class="offer-save"><span class="save-label">Save<br>up to</span><span class="save-num">20<sup>%</sup></span></div>
    </article>
    <article class="offer lemon">
      <div class="offer-name">The Lodge<br>Glowbug Cove</div>
      <div class="offer-photo" role="img" aria-label="Friends lounging on a blue float outside the lodge" style="background:linear-gradient(180deg,#8fb6d8,#9a7a6a 55%,#7fc0d6)"></div>
      <div class="offer-save"><span class="save-label">Save<br>up to</span><span class="save-num">30<sup>%</sup></span></div>
    </article>
    <article class="offer sky">
      <div class="offer-name summer">Summer<br>Savings</div>
      <div class="offer-photo" role="img" aria-label="Kids walking through an indoor splash area with a waterfall" style="background:linear-gradient(180deg,#c9ccd2,#a9b8c0 60%,#d8dde0)"></div>
      <div class="offer-save"><span class="save-label">Save<br>up to</span><span class="save-num">35<sup>%</sup></span></div>
    </article>
  </section>

  <section class="booking">
    <p class="dates">Book by March 1st,2019</p>
    <p>Stay Dates Now-May 23rd,2019</p>
    <a class="reserve" href="#">RESERVE NOW!</a>
  </section>

  <footer class="footer">
    <p class="site">www.lodgeatharrowmeadow-example.com</p>
    <p class="copy">Copyright @ 2019 lodgeatharrowmeadow-example.com</p>
  </footer>

</div>
</body>
</html>
```